Quillbrookes websites redesign

Www.quill-brookes.com needs to be redesigned along with updations. The incremental material will be provided for the updations. We are looking for complete redesign of the pages with the new content. The complete write up will be provided soon

Target Market(s)

Global

Coding

Coded - Design and coding required

Number of Pages Required

5+ page

Requirements
Must have
• A clean and slick design for the Consulting.
Should not have
• Too many pictures which reduces the speed of the site

```html
<!DOCTYPE html>
<html lang="en">
<head>
<meta charset="utf-8">
<title>Quillbrookes – Founder</title>
<link href="https://fonts.googleapis.com/css2?family=Arimo:wght@400;700&family=Montserrat:wght@400;600&display=swap" rel="stylesheet">
<style>
:root{
  --ink:#555;
  --title:#5a5a5a;
  --nav:#6a6a6a;
  --accent:#2ea3c9;
  --rule:#e6e6e6;
  --footer:#1c1c1c;
  --footer-base:#151515;
  --footer-text:#9a9a9a;
  --footer-line:#333;
  --white:#fff;
}
*{margin:0;padding:0;box-sizing:border-box}
html,body{width:1200px;height:1124px;overflow:hidden;background:var(--white)}
body{position:relative;font-family:"Arimo",Arial,sans-serif;color:var(--ink)}
.site-header{position:absolute;left:0;top:0;width:1200px;height:84px;border-bottom:1px solid var(--rule)}
.brand{position:absolute;left:163px;top:28px;display:flex;align-items:center;gap:10px;font-family:"Montserrat",sans-serif;font-size:26px;font-weight:400;color:#5b2a2a}
.brand-dot{width:32px;height:32px;border-radius:50%;background:var(--accent)}
.main-nav a{position:absolute;top:36px;font-size:13.5px;color:var(--nav);text-decoration:none}
.main-nav a.active{color:var(--accent)}
.main-nav a.active::after{content:"";position:absolute;left:1px;right:0;top:43px;height:3px;background:var(--accent)}
.founder-photo{position:absolute;left:163px;top:170px;width:321px;height:186px;background:linear-gradient(135deg,#6a4a7a,#8a4050 60%,#5a3a6a)}
.founder-bio{position:absolute;left:527px;top:164px;width:520px}
.founder-name{font-family:"Montserrat",sans-serif;font-weight:400;font-size:23px;color:var(--title);letter-spacing:.3px;margin-bottom:26px}
.founder-name strong{font-weight:600}
.founder-bio p{font-size:11.6px;line-height:17.6px;margin-bottom:17.6px}
.site-footer{position:absolute;left:0;top:767px;width:1200px;height:357px;background:var(--footer);color:var(--footer-text)}
.footer-base{position:absolute;left:0;top:300px;width:1200px;height:57px;background:var(--footer-base);border-top:1px solid var(--footer-line)}
.footer-base p{position:absolute;left:164px;top:22px;font-size:11.5px}
.footer-brand{position:absolute;left:164px;top:64px;display:flex;align-items:center;gap:8px;font-family:"Montserrat",sans-serif;font-size:20px;color:#8a8a8a}
.footer-brand .brand-dot{width:28px;height:28px;background:#8a8a8a}
.address{position:absolute;left:166px;top:115px;font-size:11.3px;line-height:19.2px;font-style:normal}
.contact-line{position:absolute;left:166px;font-size:11.5px}
.contact-line b{color:var(--accent);font-size:13px}
.contact-line a{color:var(--accent)}
.footer-col{position:absolute;top:69px}
.footer-col h3{font-family:"Montserrat",sans-serif;font-weight:400;font-size:13px;color:var(--white);letter-spacing:.2px}
.footer-col h3::after{content:"";display:block;width:29px;height:1px;background:#aaa;margin-top:13px}
.newsletter p{font-size:11.5px;margin-top:17px}
.email-field{margin-top:16px;width:201px;height:36px;border:1px solid #555;display:flex;align-items:center;justify-content:space-between;padding:0 10px 0 14px;font-size:11.5px;color:#ccc}
.site-links ul{list-style:none;margin-top:12px}
.site-links li{font-size:11.5px;line-height:24px;padding-left:16px;position:relative}
.site-links li::before{content:"»";position:absolute;left:1px;top:0;font-size:10px}
.site-links li:first-child{color:var(--accent);text-decoration:underline}
.social-row{display:flex;gap:4px;margin-top:19px}
.social-row span{width:28px;height:28px;border:2px solid #aaa;border-radius:50%}
.social-row span:first-child{border-color:var(--accent)}
</style>
</head>
<body>
<header class="site-header">
  <div class="brand"><span class="brand-dot"></span>Quillbrookes</div>
  <nav class="main-nav">
    <a href="#" style="left:581px">home</a>
    <a href="#" class="active" style="left:652px">founder</a>
    <a href="#" style="left:727px">consultancy</a>
    <a href="#" style="left:827px">platform</a>
    <a href="#" style="left:899px">case studies</a>
    <a href="#" style="left:1001px">contact</a>
  </nav>
</header>

<div class="founder-photo" role="img" aria-label="Founder speaking at a podium with flowers at a business conference"></div>

<section class="founder-bio">
  <h1 class="founder-name">MEERA <strong>SARKAR</strong></h1>
  <p>Ms. Meera Sarkar is the founder director of Quillbrookes Consultancy Limited (QCL) based at Hong Kong. Meera served as the Deputy Country Head of Corvane Trust Bank, Singapore office until Mar 2016, leading Commercial Lending business in East Asia and Trade Finance business across regions. During her tenure, both the businesses grew steadily.</p>
  <p>Meera began her banking career with Corvane Trust Bank, a leading private lender, in the year 2004 and over the next decade held several senior roles in the Commercial, Institutional and Global Banking space across South Asia, East Asia, Americas and Europe.</p>
  <p>Meera’s Commercial Banking experience includes her roles as Area Manager for the Southern Region (Food and Agri businesses) and Commercial Lending Head for East Asia where she managed complex structured transactions with a number of well known corporate clients.</p>
  <p>Meera’s Institutional banking experience includes her roles as Regional Head for Americas and Europe and Global Head of Trade Finance business where she managed relationships with over 300 financial institutions worldwide with a focus to expand business in the area of Trade, Treasury and other funded &amp; unfunded products. The responsibility also included leveraging these relationships for international fund raising for Corvane Trust Bank and she led several notable fund raising deals for the bank.</p>
  <p>Prior to joining Corvane Trust Bank, Meera worked in the engineering industry where she worked on product design, strategic planning and business modelling for Mergers &amp; Acquisitions.</p>
  <p>Meera is a management graduate from Larkfield School of Business and also holds a Masters in Economics. She has been a regular speaker at international events like the Harbour Trade Summit and Eastgate Industry Meet in various countries.</p>
</section>

<footer class="site-footer">
  <div class="footer-brand"><span class="brand-dot"></span>Quillbrookes</div>
  <address class="address">Quillbrookes Consultancy Ltd<br>Unit 05, 18th Floor, Harbourline Tower<br>8 Seaview Road, Kowloon<br>Hong Kong</address>
  <p class="contact-line" style="top:211px">T: <b>852-20001234</b></p>
  <p class="contact-line" style="top:233px">E: <a href="#">query@quill-brookes.com</a></p>

  <div class="footer-col newsletter" style="left:448px">
    <h3>GET IN TOUCH!</h3>
    <p>Simply Drop Your Mail Here</p>
    <div class="email-field">Your Email Here
      <svg width="17" height="11" viewBox="0 0 17 11"><rect width="17" height="11" fill="var(--accent)"/><path d="M0 0l8.5 6L17 0M0 11l6-5M17 11l-6-5" stroke="#fff" fill="none"/></svg>
    </div>
  </div>

  <div class="footer-col site-links" style="left:731px">
    <h3>SITE LINKS</h3>
    <ul><li>Home</li><li>Founder</li><li>Consultancy</li><li>System</li><li>Case Studies</li><li>Contact</li></ul>
  </div>

  <div class="footer-col social" style="left:916px">
    <h3>SOCIAL LINKS</h3>
    <div class="social-row"><span aria-label="Social link"></span><span aria-label="Social link"></span><span aria-label="Social link"></span><span aria-label="Social link"></span></div>
  </div>

  <div class="footer-base"><p>© Quillbrookes Consultancy Limited</p></div>
</footer>
</body>
</html>
```